We want to design total new business card and logo for Kestrel Building Services Ltd

Our company name Kestrel Building Services Ltd. Design new logo and business card , need hi-end luxury style art for architecture and construction industry. The card should simple but stylish. Our business focus on CONNECT tradesman to construction company, help marketing construction company tender oversea projects, managing franchise in construction sector, delivery amazing services to our client, so Logo should show the CONNECTION IDEA, CONNECTING PEOPLE, LUXURY. Visit our website for more information: kestrelgroup.example.nz

Target Market(s)

Directors or managers

Industry/Entity Type

Construction Company

Contact Information for Business Card

Name, Title, Mobile, Email, Website

Font styles to use
Serif

Colors

Designer to choose colors to be used in the design.

Requirements
Must have
• Simple and luxury, connection icon
Nice to have
• Special materials, plastic card, look through,...
• Look new ideas.

```html
<!DOCTYPE html>
<html lang="en">
<head>
<meta charset="utf-8">
<title>Kestrel Building Services – Business Card</title>
<link rel="stylesheet" href="https://fonts.googleapis.com/css2?family=PT+Sans:wght@700&family=Questrial&family=Open+Sans:wght@400&family=Lato:wght@400&family=Bebas+Neue&display=swap">
<style>
  :root {
    --backdrop: #2a2a2a;
    --card-light: #ededed;
    --brand-teal: #07a8c8;
    --ink: #333333;
    --rule: #8a8a8a;
    --white: #ffffff;
  }
  * { margin: 0; padding: 0; box-sizing: border-box; }
  html, body { width: 1200px; height: 1200px; overflow: hidden; }
  body { background: var(--backdrop); position: relative; }

  .card {
    position: absolute;
    top: 310px;
    height: 594px;
    text-align: center;
  }
  .card-front { left: 234px; width: 364px; background: var(--card-light); }
  .card-back { left: 627px; width: 369px; background: var(--brand-teal); }

  .brand-mark-square {
    position: absolute;
    left: 50%;
    transform: translateX(-50%);
    background: var(--brand-teal);
  }
  .card-front .brand-mark-square { top: 128px; width: 16px; height: 16px; }

  .brand-name {
    position: absolute;
    left: 0; right: 0;
    top: 180px;
    font-family: "PT Sans", sans-serif;
    font-weight: 700;
    font-size: 22px;
    color: var(--brand-teal);
    letter-spacing: 0.2px;
  }

  .person-name {
    position: absolute;
    left: 0; right: 0;
    top: 294px;
    font-family: "Questrial", sans-serif;
    font-size: 26px;
    color: var(--brand-teal);
    letter-spacing: 0.5px;
  }
  .person-title {
    position: absolute;
    left: 0; right: 0;
    top: 320px;
    font-family: "Lato", sans-serif;
    font-size: 16.5px;
    color: var(--ink);
  }

  .icon-row {
    position: absolute;
    left: 91px;
    top: 352px;
    width: 187px;
    height: 24px;
    display: flex;
    align-items: center;
    justify-content: center;
    gap: 2px;
  }
  .icon-row .rule-side { flex: 1; height: 1px; background: var(--rule); }
  .icon-row .rule-side:first-child { margin-right: 6px; }
  .icon-row .rule-side:last-child { margin-left: 6px; }
  .contact-icon { width: 23px; height: 23px; display: block; }

  .contact-list {
    position: absolute;
    left: 0; right: 0;
    top: 386px;
    font-family: "Open Sans", sans-serif;
    font-size: 16.5px;
    line-height: 21.5px;
    color: var(--ink);
    list-style: none;
  }

  .divider {
    position: absolute;
    left: 91px;
    width: 187px;
    top: 482px;
    height: 1px;
    background: var(--rule);
  }

  .company-legal {
    position: absolute;
    left: 0; right: 0;
    top: 492px;
    font-family: "Open Sans", sans-serif;
    font-size: 17px;
    color: var(--brand-teal);
  }
  .company-address {
    position: absolute;
    left: 0; right: 0;
    top: 514px;
    font-family: "Open Sans", sans-serif;
    font-size: 16.5px;
    line-height: 21.5px;
    color: var(--ink);
    font-style: normal;
  }

  .card-back .brand-mark-square {
    top: 220px;
    width: 22px;
    height: 22px;
    background: var(--white);
  }
  .back-brand-name {
    position: absolute;
    left: 0; right: 0;
    top: 262px;
    font-family: "PT Sans", sans-serif;
    font-weight: 700;
    font-size: 34px;
    line-height: 40px;
    color: var(--white);
    letter-spacing: 1px;
  }
  .tagline {
    position: absolute;
    left: 0; right: 0;
    top: 508px;
    font-family: "Bebas Neue", sans-serif;
    font-size: 26px;
    color: #d9f3f9;
    letter-spacing: 0.2px;
  }
</style>
</head>
<body>

  <section class="card card-front" aria-label="Business card front">
    <span class="brand-mark-square" aria-hidden="true"></span>
    <h1 class="brand-name">KESTREL BUILDING SERVICES</h1>

    <h2 class="person-name">MARCUS HALE</h2>
    <p class="person-title">Managing Director</p>

    <div class="icon-row" aria-hidden="true">
      <span class="rule-side"></span>
      <svg class="contact-icon" viewBox="0 0 24 24">
        <circle cx="12" cy="12" r="11.5" fill="#07a8c8"/>
        <circle cx="12" cy="12" r="8.5" fill="none" stroke="#fff" stroke-width="1.3"/>
        <path d="M7.5 10.5 Q12 6.5 16.5 10.5 L15.5 12 L13.5 11 L13.5 10 Q12 9.5 10.5 10 L10.5 11 L8.5 12 Z M9 13 H15 L16 16 H8 Z" fill="#fff"/>
      </svg>
      <svg class="contact-icon" viewBox="0 0 24 24">
        <circle cx="12" cy="12" r="11.5" fill="#07a8c8"/>
        <circle cx="12" cy="12" r="8.5" fill="none" stroke="#fff" stroke-width="1.3"/>
        <path d="M7.5 10.5 Q12 6.5 16.5 10.5 L15.5 12 L13.5 11 L13.5 10 Q12 9.5 10.5 10 L10.5 11 L8.5 12 Z M9 13 H15 L16 16 H8 Z" fill="#fff"/>
      </svg>
      <svg class="contact-icon" viewBox="0 0 24 24">
        <circle cx="12" cy="12" r="11.5" fill="#07a8c8"/>
        <circle cx="12" cy="12" r="8.5" fill="none" stroke="#fff" stroke-width="1.3"/>
        <rect x="7.5" y="9" width="9" height="6.5" fill="none" stroke="#fff" stroke-width="1.2"/>
        <path d="M7.5 9 L12 12.8 L16.5 9" fill="none" stroke="#fff" stroke-width="1.2"/>
      </svg>
      <svg class="contact-icon" viewBox="0 0 24 24">
        <circle cx="12" cy="12" r="11.5" fill="#07a8c8"/>
        <circle cx="12" cy="12" r="8.5" fill="none" stroke="#fff" stroke-width="1.3"/>
        <circle cx="12" cy="12" r="4.6" fill="none" stroke="#fff" stroke-width="1.2"/>
        <path d="M7.4 12 H16.6 M12 7.4 Q9.5 12 12 16.6 Q14.5 12 12 7.4" fill="none" stroke="#fff" stroke-width="1"/>
      </svg>
      <span class="rule-side"></span>
    </div>

    <ul class="contact-list">
      <li>0800 555 010</li>
      <li>021 555 0147</li>
      <li>info@kestrelgroup.example.nz</li>
      <li>www.kestrelgroup.example.nz</li>
    </ul>

    <span class="divider" aria-hidden="true"></span>

    <p class="company-legal">KESTREL BUILDING SERVICES LTD</p>
    <address class="company-address">12 Harbour Lane, Westgate,<br>Auckland 2099, New Zealand</address>
  </section>

  <section class="card card-back" aria-label="Business card back">
    <span class="brand-mark-square" aria-hidden="true"></span>
    <p class="back-brand-name">KESTREL<br>BUILDING SERVICES</p>
    <p class="tagline">AMAZING SERVICES AFFORDABLE PRICE</p>
  </section>

</body>
</html>
```